Sea Shipping Logistics Company

The business is a logistics company (sea shipping and other special logistics) and also sales of bulk building materials.
The Design should be minimalistic and give a feeling of power and connectivity.
When the client sees the card, they should get a feeling of confident. Dark overall color (background) and print should be red / white .See logo. The card will be printed on trifecta with the middle color being red.

One side should be the logo and a 5 / 6 word slogan
And other side name, contact (phone/email) and a QR Code.

Target Market(s)

Construction companies / Oil & Gas related companies

Industry/Entity Type

Sea Bulk Shipping Logistics

Contact Information for Business Card

Name, Telephone number, Email address, Website URL, QR Code (see description)

Font styles to use
Sans Serif

Requirements
Must have
• No idea
Nice to have
• Minimalistic, but strong and powerful look and feel.

```html
<!DOCTYPE html>
<html lang="en">
<head>
<meta charset="UTF-8">
<title>Orla Business Card</title>
<link href="https://fonts.googleapis.com/css2?family=Arimo:wght@400;700&display=swap" rel="stylesheet">
<style>
  :root {
    --backdrop: #e3e3e3;
    --card-black: #000000;
    --card-pattern-dark: #0a0a0a;
    --card-pattern-light: #161616;
    --brand-red: #e8232b;
    --ink-white: #ffffff;
    --corner: 69px;
  }
  * { margin: 0; padding: 0; box-sizing: border-box; }
  html, body {
    width: 1200px;
    height: 900px;
    overflow: hidden;
  }
  body {
    position: relative;
    background: var(--backdrop);
    font-family: "Arimo", Arial, sans-serif;
    color: var(--ink-white);
  }
  .card {
    position: absolute;
    top: 216px;
    width: 309px;
    height: 501px;
    background: var(--card-black);
    box-shadow: 2px 3px 6px rgba(0, 0, 0, 0.35);
    overflow: hidden;
  }
  .card--front {
    left: 279px;
    border-radius: 0 var(--corner) 0 var(--corner);
  }
  .card--back {
    left: 617px;
    border-radius: var(--corner) 0 var(--corner) 0;
  }
  .card__texture {
    position: absolute;
    inset: 0;
    background: linear-gradient(160deg, var(--card-pattern-light), var(--card-pattern-dark));
  }
  .brand {
    position: absolute;
    display: flex;
    align-items: flex-start;
  }
  .card--front .brand { left: 38px; top: 371px; }
  .card--back .brand { left: 37px; top: 126px; }
  .brand__square {
    width: 81px;
    height: 79px;
    border: 2px solid var(--ink-white);
    flex-shrink: 0;
  }
  .brand__text {
    margin-left: 6px;
    display: flex;
    flex-direction: column;
    padding-top: 9px;
    width: 150px;
  }
  .brand__name {
    font-weight: 700;
    font-size: 49px;
    line-height: 44px;
    letter-spacing: -0.5px;
    color: var(--ink-white);
  }
  .brand__tagline {
    font-weight: 400;
    font-size: 11.5px;
    line-height: 14px;
    margin-top: 1px;
    letter-spacing: 0.1px;
    white-space: nowrap;
    color: var(--ink-white);
  }
  .person {
    position: absolute;
    left: 32px;
    top: 334px;
  }
  .person__name {
    font-weight: 700;
    font-size: 22px;
    line-height: 22px;
    color: var(--brand-red);
  }
  .person__role {
    font-weight: 400;
    font-size: 15.5px;
    line-height: 17px;
    color: var(--ink-white);
  }
  .contact {
    position: absolute;
    left: 32px;
    top: 386px;
    list-style: none;
  }
  .contact__item {
    display: flex;
    align-items: center;
    font-size: 15px;
    line-height: 18px;
    height: 18px;
  }
  .contact__icon {
    width: 13px;
    height: 13px;
    margin-right: 5px;
    flex-shrink: 0;
  }
</style>
</head>
<body>

  <section class="card card--front">
    <div class="card__texture" role="img" aria-label="Repeating grid of faint brand marks across the card"></div>
    <div class="brand">
      <div class="brand__square"></div>
      <div class="brand__text">
        <span class="brand__name">ORLA</span>
        <span class="brand__tagline">FREIGHT &amp; BULK SUPPLY</span>
      </div>
    </div>
  </section>

  <section class="card card--back">
    <div class="brand">
      <div class="brand__square"></div>
      <div class="brand__text">
        <span class="brand__name">ORLA</span>
        <span class="brand__tagline">FREIGHT &amp; BULK SUPPLY</span>
      </div>
    </div>

    <div class="person">
      <p class="person__name">MARCUS REID</p>
      <p class="person__role">MANAGING DIRECTOR</p>
    </div>

    <ul class="contact">
      <li class="contact__item">
        <svg class="contact__icon" viewBox="0 0 16 16" aria-hidden="true">
          <path d="M3.5 1.5 L6 4.5 L4.6 6.2 C5.5 8 7.8 10.4 9.8 11.4 L11.5 10 L14.5 12.5 L13 14.5 C7.5 14.5 1.5 8.5 1.5 3 Z" fill="none" stroke="var(--brand-red)" stroke-width="1.6" stroke-linejoin="round"/>
          <path d="M9.5 1.5 A5 5 0 0 1 14.5 6.5 M9.5 4 A2.5 2.5 0 0 1 12 6.5" fill="none" stroke="var(--brand-red)" stroke-width="1.4"/>
        </svg>
        <span>044-987 654 321</span>
      </li>
      <li class="contact__item">
        <svg class="contact__icon" viewBox="0 0 16 16" aria-hidden="true">
          <rect x="1" y="3" width="14" height="10" fill="var(--brand-red)"/>
          <path d="M1 3 L8 9 L15 3 M1 13 L6 7.5 M15 13 L10 7.5" fill="none" stroke="var(--card-black)" stroke-width="1"/>
        </svg>
        <span>hello@orlafreight.com</span>
      </li>
      <li class="contact__item">
        <svg class="contact__icon" viewBox="0 0 16 16" aria-hidden="true">
          <g fill="none" stroke="var(--brand-red)" stroke-width="1.3">
            <circle cx="8" cy="8" r="6.5"/>
            <ellipse cx="8" cy="8" rx="2.8" ry="6.5"/>
            <path d="M1.5 8 H14.5 M2.5 4.8 H13.5 M2.5 11.2 H13.5"/>
          </g>
        </svg>
        <span>www.orlafreight.com</span>
      </li>
    </ul>
  </section>

</body>
</html>
```